Keystone Trench Co Business Card*

Looking for a professional, clean and crisp business card

I am in the underground utilities industry and am just looking for a really impressive business card. I would like our card to be white with our symbol crisp and clear with it protruding. I also have a business partner that will require his name and info on the card once the design is set. I would like to have our website info on the card which is;
http://keystonetrenchco.example/

Contact Information for Business Card

Website, contact name, number and email

```html
<!DOCTYPE html>
<html lang="en">
<head>
<meta charset="utf-8">
<title>Keystone Trench Co — Business Card</title>
<link rel="stylesheet" href="https://fonts.googleapis.com/css2?family=Oswald:wght@600&family=Montserrat:wght@400;500&display=swap">
<style>
  :root {
    --stage: #1c1d20;
    --card-white: #ffffff;
    --card-black: #0b0d11;
    --slate: #323b48;
    --ink: #1f2429;
    --brand-blue: #4467b9;
    --pipe-grey: #3a424e;
  }
  * { box-sizing: border-box; margin: 0; padding: 0; }
  html, body { width: 1200px; height: 900px; overflow: hidden; }
  body {
    background: var(--stage);
    display: flex;
    align-items: center;
    justify-content: center;
    gap: 110px;
    font-family: "Montserrat", sans-serif;
  }
  .card {
    width: 360px;
    height: 630px;
    border-radius: 4px;
    position: relative;
    overflow: hidden;
    box-shadow: 0 18px 40px rgba(0,0,0,.55);
  }

  /* Back side */
  .card--back { background: var(--card-black); }
  .back__pattern {
    position: absolute;
    inset: 0;
    background: linear-gradient(160deg, #0b0d11 0%, var(--pipe-grey) 45%, #0b0d11 60%, var(--pipe-grey) 80%, #0b0d11 100%);
    opacity: .55;
  }
  .back__tab {
    position: absolute;
    left: 0; right: 0; top: 0;
    height: 360px;
    background: var(--slate);
    border-radius: 0 0 180px 180px;
    display: flex;
    align-items: center;
    justify-content: center;
    gap: 12px;
    padding: 0 34px;
  }
  .back__tab .brand-name { color: #ffffff; }

  /* Brand lockup */
  .brand {
    display: flex;
    align-items: center;
    gap: 12px;
  }
  .brand-dot {
    width: 22px; height: 22px;
    border-radius: 50%;
    background: var(--brand-blue);
    flex: none;
  }
  .brand-name {
    font-family: "Oswald", sans-serif;
    font-weight: 600;
    font-size: 30px;
    line-height: 1.1;
    letter-spacing: 1px;
    text-transform: uppercase;
    color: var(--ink);
  }

  /* Front side */
  .card--front {
    background: var(--card-white);
    display: flex;
    flex-direction: column;
    align-items: center;
    padding: 90px 38px 0;
  }
  .front__brand { height: 200px; }
  .contact {
    margin-top: 90px;
    width: 100%;
    border-top: 1.5px solid var(--brand-blue);
    border-bottom: 1.5px solid var(--brand-blue);
    padding: 30px 0 28px;
    text-align: center;
  }
  .contact__name {
    font-family: "Oswald", sans-serif;
    font-weight: 600;
    font-size: 26px;
    letter-spacing: 1.5px;
    text-transform: uppercase;
    color: var(--ink);
  }
  .contact__icons {
    display: flex;
    justify-content: center;
    gap: 14px;
    margin: 16px 0 14px;
  }
  .contact__icons svg { width: 18px; height: 18px; }
  .contact__line {
    font-size: 15px;
    color: var(--ink);
    line-height: 1.6;
  }
  .contact__web { color: var(--ink); text-decoration: none; }
  .contact__web strong { color: var(--brand-blue); font-weight: 500; }
</style>
</head>
<body>

  <section class="card card--back" aria-label="Card back">
    <div class="back__pattern" role="img" aria-label="Diagonal rows of dark pipe sections"></div>
    <div class="back__tab">
      <div class="brand">
        <span class="brand-dot"></span>
        <span class="brand-name">Keystone Trench Co</span>
      </div>
    </div>
  </section>

  <section class="card card--front" aria-label="Card front">
    <div class="brand front__brand">
      <span class="brand-dot"></span>
      <span class="brand-name">Keystone Trench Co</span>
    </div>

    <div class="contact">
      <h1 class="contact__name">Dale Marchetti</h1>
      <div class="contact__icons" aria-hidden="true">
        <svg viewBox="0 0 20 20"><circle cx="10" cy="10" r="8.5" fill="none" stroke="var(--brand-blue)" stroke-width="1.6"/><path d="M7 6.2c.5-.4 1-.3 1.3.2l.7 1.2c.2.4.1.8-.2 1l-.5.4c.4.9 1.1 1.6 2 2l.4-.5c.3-.3.7-.4 1-.2l1.2.7c.5.3.6.8.2 1.3-.6.8-1.5 1-2.4.6-1.9-.8-3.3-2.2-4.1-4.1-.4-.9-.2-1.8.4-2.6z" fill="var(--brand-blue)"/></svg>
        <svg viewBox="0 0 20 20"><rect x="2.5" y="5" width="15" height="10" rx="1" fill="none" stroke="var(--brand-blue)" stroke-width="1.6"/><path d="M3 5.5l7 5.5 7-5.5" fill="none" stroke="var(--brand-blue)" stroke-width="1.6"/></svg>
        <svg viewBox="0 0 20 20"><circle cx="10" cy="10" r="8" fill="var(--brand-blue)"/><path d="M2 10h16M10 2c-3 3-3 13 0 16M10 2c3 3 3 13 0 16" fill="none" stroke="#fff" stroke-width="1.2"/></svg>
      </div>
      <p class="contact__line">555-014-2296</p>
      <p class="contact__line">dale@keystonetrenchco.example</p>
      <p class="contact__line"><a class="contact__web" href="http://keystonetrenchco.example/">www.<strong>keystonetrenchco</strong>.example</a></p>
    </div>
  </section>

</body>
</html>
```